Brochure for a civil enineering company in A4 format

I need a brochure design for our company TIRO Engineering S.r.l.. We are an engineering consultant company. Our main clients are from the infrastructure industry (geotechnical and underground sectors mainly).
We are looking for a 2 pages (4 faces) fold out design with a glued pocket where we can put individual data sheets.
I need A4 format pages.

Target Market(s)

We are an engineering consultant company. Our main clients are from the infrastructure industry (geotechnical and underground sectors mainly).

Industry/Entity Type

Civil Engineer

Font styles to use
Sans Serif

Requirements
Must have
• Overall: 2 pages in A4 format
Essential style. Bright and modern appearance.
Glued pocket
Logo integrated in a picture on the pocket where I would like to insert a slogan (… tiro engineering … reliable solutions …)
Attached are selected images which the designer can use and edit at their own discretion.
Some advice in the following (anyway designers are free to provide their solutions):
Outer sheets:
Front page with name, logo. It could be nice to have the “m” of the logo integrated in a pictures, also a modified picture (I mean modify one of the attached pictures) so to create a general image and do not tie the cover to a specific job.
Back page: offices address and contact email address. Nice to have one space for a slogan.
Inner sheet: text that I upload in the file “inside-sheets”, possibly with pictures on each sheet. In the right faces insert the glued pocket. On this pages insert the section OUR EXPERIENCE ….with a space for a picture of our team.
Nice to have
• Clean and essential design.
Pictures choosing from the atteched ones. Pictures could be modified in a very light manner to make them a general idea of the work ( I mean geotechnical world) without to be immediately linked to a specific site.
Should not have
• excessive frills

```html
<!DOCTYPE html>
<html lang="it">
<head>
<meta charset="utf-8">
<title>TIRO Engineering – Brochure</title>
<link href="https://fonts.googleapis.com/css2?family=Montserrat:wght@300;400;500;600;700&family=Roboto+Slab:wght@400&display=swap" rel="stylesheet">
<style>
  :root{
    --stage:#666666;
    --paper:#f1f1f1;
    --paper-light:#fafafa;
    --ink:#1d1d1d;
    --ink-soft:#6e6e6e;
    --ink-body:#3c3c3c;
    --rule:#2a2a2a;
    --tone-mid:#d6d6d6;
    --photo-dark:#1a1a1a;
  }
  *{box-sizing:border-box;margin:0;padding:0}
  html,body{width:888px;height:1200px;overflow:hidden}
  body{background:var(--stage);font-family:"Montserrat",sans-serif;color:var(--ink);position:relative}

  .spread{position:absolute;left:34px;width:820px;height:580px;overflow:hidden;
    background:linear-gradient(90deg,var(--paper) 0 50%,var(--paper-light) 50% 100%)}
  .spread--outer{top:20px}
  .spread--inner{top:610px}
  .face{position:absolute;top:0;height:100%;width:410px}
  .face--left{left:0;background:linear-gradient(160deg,#e9e9e9 0%,#f4f4f4 45%,#ededed 100%)}
  .face--right{left:410px;background:linear-gradient(200deg,#f0f0f0 0%,#fbfbfb 50%,#f5f5f5 100%)}

  .texture-dots{position:absolute;left:0;top:0;width:200px;height:230px;
    background:linear-gradient(135deg,var(--tone-mid),rgba(230,230,230,0));opacity:.7}
  .texture-block{position:absolute;left:125px;top:46px;width:203px;height:205px;
    background:linear-gradient(135deg,#dcdcdc,#e8e8e8)}

  .section-title{position:absolute;font-size:13.5px;font-weight:300;letter-spacing:.2px;
    padding-bottom:5px;border-bottom:1px solid var(--rule)}
  .section-title strong{font-weight:600}

  /* outer spread */
  .offices-title{left:42px;top:353px;width:180px}
  .office{position:absolute;left:42px;font-size:8.2px;font-weight:500;line-height:1.35}
  .office .city{padding-left:14px}
  .office .row{display:flex;align-items:flex-start;gap:6px}
  .office .row svg{width:8px;height:8px;flex:none;margin-top:1px}
  .office .indent{padding-left:14px}
  .office--milano{top:388px}
  .office--arco{top:461px}
  .office--web{top:534px}

  .brand-small{position:absolute;left:276px;top:515px;text-align:center}
  .brand-small .name{font-size:26px;font-weight:700;letter-spacing:-.5px;line-height:1}
  .brand-small .tag{font-size:3.6px;letter-spacing:.9px;margin-top:2px}

  .brand-cover{position:absolute;left:538px;top:36px;font-size:50px;font-weight:700;letter-spacing:-1.5px;line-height:1}

  .photo-frame{position:absolute;left:270px;top:122px;width:550px;height:336px;background:#fff}
  .photo{position:absolute}
  .photo--tunnel{left:276px;top:127px;width:333px;height:325px;
    background:radial-gradient(ellipse at 68% 78%,#cfcfcf 0%,#5a5a5a 22%,var(--photo-dark) 55%,#0b0b0b 100%)}
  .photo--site{left:614px;top:127px;width:200px;height:179px;
    background:linear-gradient(135deg,#9a9895,#b9b5ae 40%,#8a7d70 70%,#a9a49c)}
  .photo--yard{left:614px;top:311px;width:200px;height:141px;
    background:linear-gradient(160deg,#9ea3a0,#b8b8b4 45%,#8a9a80 80%,#5f7b4f)}

  .slogan{position:absolute;left:446px;top:479px;width:340px;text-align:center;white-space:nowrap;
    font-family:"Roboto Slab",serif;font-size:17px;letter-spacing:-.8px;line-height:20px}

  /* inner spread */
  .company-title{left:42px;top:34px;width:326px}
  .services-title{left:42px;top:250px;width:326px}
  .expertise-title{left:451px;top:34px;width:326px}
  .copy{position:absolute;font-size:6.8px;font-weight:300;line-height:1.42;color:var(--ink-soft);text-align:justify}
  .copy p{margin-bottom:7px}
  .copy--company{left:42px;top:71px;width:326px}
  .copy--services{left:42px;top:285px;width:326px}
  .copy--highlight{position:absolute;left:42px;top:397px;width:326px;font-size:6.8px;font-weight:500;line-height:1.42;color:var(--ink);text-align:justify}
  .thumb{position:absolute;left:42px;width:90px;height:56px}
  .thumb--pit{top:439px;background:linear-gradient(180deg,#8f9495,#6c706e 50%,#4e5250)}
  .thumb--station{top:499px;background:linear-gradient(180deg,#b7c1c8,#a6a29b 45%,#6e6a63)}
  .copy--list{left:146px;top:440px;width:222px;font-size:5.9px;line-height:1.45}
  .copy--list p{margin-bottom:6px}
  .bottom-bar{position:absolute;left:0;bottom:0;width:410px;height:4px;background:var(--ink)}

  .copy--intro{left:451px;top:71px;width:326px;color:var(--ink-body);font-weight:400}
  .founders-tab{position:absolute;left:450px;top:121px;width:326px;height:15px;border-bottom:1px solid var(--rule)}
  .founders-tab span{display:inline-block;height:15px;padding:0 18px 0 12px;background:var(--ink);color:#fff;
    font-size:8.4px;font-weight:500;line-height:15px;clip-path:polygon(0 0,92% 0,100% 100%,0 100%)}
  .copy--bios{left:451px;top:150px;width:326px;font-size:5.8px;line-height:1.48;color:var(--ink-body)}
  .copy--bios p{margin-bottom:9px}
  .photo--portals{left:421px;top:456px;width:399px;height:124px;
    background:linear-gradient(180deg,#d9e6ef 0%,#c4d0d6 25%,#a9a493 45%,#8f8a7c 70%,#6f6a5f 100%);
    clip-path:polygon(14% 0,100% 0,100% 100%,0 100%,6% 30%)}
</style>
</head>
<body>

<section class="spread spread--outer" aria-label="Copertina e retro">
  <div class="face face--left"></div>
  <div class="face face--right"></div>
  <div class="texture-dots"></div>
  <div class="texture-block"></div>

  <h2 class="section-title offices-title">OUR <strong>OFFICES</strong></h2>

  <div class="office office--milano">
    <div class="city">Milano</div>
    <div class="row"><svg viewBox="0 0 10 10"><circle cx="5" cy="3.5" r="2.3" fill="none" stroke="#1d1d1d" stroke-width="1"/><path d="M5 5.8V9.5M3 9.5h4" stroke="#1d1d1d" stroke-width="1"/></svg><span>Via Verdi, 14</span></div>
    <div class="indent">20121 Milano - IT</div>
    <div class="row" style="margin-top:3px"><svg viewBox="0 0 10 10"><circle cx="5" cy="5" r="4.3" fill="none" stroke="#1d1d1d" stroke-width="1"/><path d="M3.5 3c.2 2 1.5 3.5 3.5 4" stroke="#1d1d1d" stroke-width="1" fill="none"/></svg><span>+39 02 5550142</span></div>
    <div class="row"><svg viewBox="0 0 10 10"><rect x="1" y="2.5" width="8" height="5.5" fill="none" stroke="#1d1d1d" stroke-width="1"/><path d="M1 2.5l4 3 4-3" stroke="#1d1d1d" stroke-width="1" fill="none"/></svg><span>info@tiroengineering.org</span></div>
  </div>

  <div class="office office--arco">
    <div class="city">Arco TN</div>
    <div class="row"><svg viewBox="0 0 10 10"><circle cx="5" cy="3.5" r="2.3" fill="none" stroke="#1d1d1d" stroke-width="1"/><path d="M5 5.8V9.5M3 9.5h4" stroke="#1d1d1d" stroke-width="1"/></svg><span>Via Lunga, 9</span></div>
    <div class="indent">38062 Arco TN - IT</div>
    <div class="row" style="margin-top:3px"><svg viewBox="0 0 10 10"><circle cx="5" cy="5" r="4.3" fill="none" stroke="#1d1d1d" stroke-width="1"/><path d="M3.5 3c.2 2 1.5 3.5 3.5 4" stroke="#1d1d1d" stroke-width="1" fill="none"/></svg><span>+39 02 5550142</span></div>
    <div class="row"><svg viewBox="0 0 10 10"><rect x="1" y="2.5" width="8" height="5.5" fill="none" stroke="#1d1d1d" stroke-width="1"/><path d="M1 2.5l4 3 4-3" stroke="#1d1d1d" stroke-width="1" fill="none"/></svg><span>info@tiroengineering.org</span></div>
  </div>

  <div class="office office--web">
    <div class="row"><svg viewBox="0 0 10 10"><circle cx="5" cy="5" r="4.2" fill="none" stroke="#1d1d1d" stroke-width="1"/><ellipse cx="5" cy="5" rx="1.8" ry="4.2" fill="none" stroke="#1d1d1d" stroke-width=".8"/><path d="M1 5h8" stroke="#1d1d1d" stroke-width=".8"/></svg><span>www.tiroengineering.org</span></div>
  </div>

  <div class="brand-small">
    <div class="name">tiro</div>
    <div class="tag">TIRO ENGINEERING . RELIABLE SOLUTIONS</div>
  </div>

  <div class="brand-cover">tiro</div>

  <div class="photo-frame"></div>
  <div class="photo photo--tunnel" role="img" aria-label="Galleria in costruzione con centine e un operaio in controluce"></div>
  <div class="photo photo--site" role="img" aria-label="Vista aerea di un cantiere con gru e materiali"></div>
  <div class="photo photo--yard" role="img" aria-label="Vista aerea di un'area di cantiere tra il verde"></div>

  <p class="slogan">TIRO ENGINEERING, RELIABLE SOLUTIONS</p>
</section>

<section class="spread spread--inner" aria-label="Pagine interne">
  <div class="face face--left"></div>
  <div class="face face--right"></div>
  <div class="texture-dots"></div>

  <h2 class="section-title company-title">OUR <strong>COMPANY</strong></h2>
  <div class="copy copy--company">
    <p>TIRO Engineering S.r.l. offre servizi di consulenza tecnica, contrattuale e strategica ai principali attori nei settori delle scienze geologiche, dell'ingegneria geotecnica e dell'ingegneria idraulica. Lavoriamo per mitigare il rischio e ridurre l'incertezza, con flessibilità nella ricerca della soluzione ottimale contribuendo ad aumentare la redditività del progetto.</p>
    <p>TIRO Engineering S.r.l. è una società indipendente che nasce nel luglio 2020 dall'associazione di un gruppo di professionisti che hanno messo a fattor comune la reciproca esperienza maturata in oltre trent'anni di attività come progettisti e consulenti nel settore delle grandi opere di ingegneria civile lavorando come Direttori Tecnici e come liberi professionisti.</p>
    <p>TIRO Engineering S.r.l. vuole unire l'esperienza dei Fondatori e delle figure chiave con l'entusiasmo di chi intraprende una nuova attività, per dare vita ad una nuova realtà che si pone come obiettivo principale il design of infrastructures that are safe, sustainable and economic.</p>
    <p>Each of our projects represents a long term commitment, we believe in providing safe, reliable, sustainable and innovative solutions. This is and will be our distinctive characteristic.</p>
  </div>

  <h2 class="section-title services-title">OUR <strong>SERVICES</strong></h2>
  <div class="copy copy--services">
    <p>Progettazione e consulenza specialistica nel campo della geologia, dell'ingegneria geotecnica, delle opere sotterranee e dell'ingegneria idraulica.</p>
    <p>Aiutiamo i nostri clienti a risolvere problemi di natura progettuale, contrattuale e costruttiva che possono nascere nell'intera vita del progetto portando la nostra esperienza all'interno delle loro organizzazioni, migliorando la qualità dei loro servizi di ingegneria, ottimizzando i loro progetti, proponendo nuove idee e soluzioni.</p>
    <p>TIRO Engineering è in grado di fornire la propria assistenza nell'intero iter procedurale, dalla fase di indagine preliminare e di analisi di fattibilità fino alla progettazione costruttiva e all'assistenza tecnica in fase realizzativa.</p>
  </div>
  <p class="copy--highlight">La specializzazione e l'esperienza accumulate nelle discipline della geologia, dell'ingegneria geotecnica e del sottosuolo e dell'idraulica ci permette di massimizzare la nostra efficacia quando sia necessario:</p>

  <div class="thumb thumb--pit" role="img" aria-label="Scavo di cantiere con paratie e imbocco di galleria"></div>
  <div class="thumb thumb--station" role="img" aria-label="Cantiere urbano davanti a un edificio storico"></div>
  <div class="copy copy--list">
    <p>far fronte a situazioni di emergenza anche su progetti in fase di sviluppo avanzato garantendo l'immediata focalizzazione delle problematiche di progetto e il risultato finale atteso (in termini di qualità, tempistiche e costi...)</p>
    <p>fornire "second opinion" di elevato valore tecnico ed amministrativo in occasione di problematiche progettuali e costruttive e dispute legali</p>
    <p>analizzare in tempi brevi progetti svolti da terzi individuandone le "criticità", verificandone la cantierabilità e la validità tecnico economica.</p>
    <p>ottimizzare i progetti redatti da terzi implementandone il contenuto e massimizzando l'efficacia economica degli investimenti.</p>
  </div>
  <div class="bottom-bar"></div>

  <h2 class="section-title expertise-title">OUR <strong>EXPERTISE AND EXPERIENCE</strong></h2>
  <div class="copy copy--intro">
    <p>La società nasce dall'associazione di un gruppo di professionisti, con indiscusse competenze ed affidabilità, con esperienza maturata in oltre trent'anni di attività come progettisti e consulenti nel settore delle grandi opere di ingegneria civile; geologia, ingegneria geotecnica ed idraulica ed opere sotterranee sono il "core" delle loro competenze.</p>
  </div>
  <div class="founders-tab"><span>I SOCI FONDATORI SONO:</span></div>
  <div class="copy copy--bios">
    <p>Marco. Già Direttore Tecnico e Socio di Qorvanti Srl, nel periodo di sua permanenza fino al dicembre 2018, ha per essa firmato tutti i progetti nel campo delle opere sotterranee e la maggior parte di quelli di ingegneria geotecnica. Da gennaio 2019 è Direttore Tecnico di Zelbrino. Può vantare più di 150 gallerie naturali e numerosi progetti ed assistenze tecniche nel campo delle strutture geotecniche, delle sistemazioni idrogeologiche e dei versanti e delle opere di protezione ambientale. Negli ultimi dieci anni è stato responsabile di attività di assistenza tecnica, per imprese di costruzione, di opere il cui valore supera i 440 Mio EUR e di servizi di progettazione definitiva e/o esecutiva per opere il cui valore supera i 1.400 Mio EUR. Ha svolto attività di verifica e validazione, in Italia ed all'estero, di numerosi progetti il cui valore complessivo supera i 3.400 Mio EUR.</p>
    <p>Piero. 30 anni di esperienza professionale. Coinvolto in più di 150 gallerie naturali con lunghezza complessiva superiore a 360 km. Numerosi progetti ed attività di assistenza tecnica nel campo delle strutture, delle sistemazioni idrogeologiche e dei versanti e delle opere di protezione ambientale. Negli ultimi dieci anni responsabile di attività di assistenza tecnica in corso d'opera, per imprese di costruzione, di opere il cui valore supera i 440 Mio EUR e di servizi di progettazione definitiva o esecutiva per opere il cui valore supera i 1.400 Mio EUR. Ha svolto attività di verifica ai fini della validazione, in Italia ed all'estero, di numerosi progetti il cui valore complessivo supera i 3.400 Mio EUR.</p>
    <p>Laura. 30 anni di esperienza professionale. Coinvolta in più di 150 gallerie naturali con lunghezza complessiva superiore a 360 km. Numerosi progetti ed attività di assistenza tecnica nel campo delle strutture, delle sistemazioni idrogeologiche e dei versanti e delle opere di protezione ambientale. Negli ultimi dieci anni responsabile di attività di assistenza tecnica in corso d'opera, per imprese di costruzione, di opere il cui valore supera i 440 Mio EUR e di servizi di progettazione definitiva o esecutiva per opere il cui valore supera i 1.400 Mio EUR. Ha svolto attività di verifica ai fini della validazione, in Italia ed all'estero, di numerosi progetti il cui valore complessivo supera i 3.400 Mio EUR.</p>
    <p>Giulia. 30 anni di esperienza professionale. Coinvolta in più di 150 gallerie naturali con lunghezza complessiva superiore a 360 km. Numerosi progetti ed attività di assistenza tecnica nel campo delle strutture, delle sistemazioni idrogeologiche e dei versanti e delle opere di protezione ambientale. Negli ultimi dieci anni responsabile di attività di assistenza tecnica in corso d'opera, per imprese di costruzione, di opere il cui valore supera i 440 Mio EUR e di servizi di progettazione definitiva o esecutiva per opere il cui valore supera i 1.400 Mio EUR. Ha svolto attività di verifica ai fini della validazione, in Italia ed all'estero, di numerosi progetti il cui valore complessivo supera i 3.400 Mio EUR.</p>
  </div>

  <div class="photo photo--portals" role="img" aria-label="Cantiere con due imbocchi di galleria, gru e colline sullo sfondo"></div>
</section>

</body>
</html>
```